Dultavo.com webside

I want to build a Dultavo.com retail website use on Shopify, reselling three main categories: Office Supplies, Packing Supplies, and Home Consumables. I also wish the webpage has the same functions as the Zelvik home page. The page is split into three different parts with the top being a sliding screen showcasing promotion products, below it being the three categories, and finally, a moving screen showing company missions.
Target Market(s)
U.S online
Industry/Entity Type
Office Supplies, packing Supplies and Home Consumables
Coding
Coded - Design and coding required
Number of Pages Required
5+ page
Look and feel

```html
<!DOCTYPE html>
<html lang="en">
<head>
<meta charset="utf-8">
<title>Dultavo — Office, Packing &amp; Home Supplies</title>
<link href="https://fonts.googleapis.com/css2?family=DM+Serif+Display&family=Mulish:wght@400;600;700;800&display=swap" rel="stylesheet">
<style>
:root{
  --teal:#00a98a;
  --ink:#1c1c1c;
  --body:#333333;
  --mint:#e9f7f5;
  --white:#ffffff;
  --serif:"DM Serif Display", Georgia, serif;
  --sans:"Mulish", Arial, sans-serif;
}
*{box-sizing:border-box;margin:0;padding:0}
html,body{width:1200px;height:2730px;overflow:hidden;background:var(--white);font-family:var(--sans);color:var(--body)}
.page{position:relative;width:1200px;height:2730px}
.btn{position:absolute;display:flex;align-items:center;justify-content:center;background:var(--teal);color:var(--white);font-family:var(--sans);font-weight:800;text-transform:uppercase;letter-spacing:.3px}
.heading{position:absolute;left:0;width:1200px;text-align:center;font-family:var(--serif);font-weight:400;color:var(--ink);font-size:25px}
.rule{position:absolute;left:586px;width:28px;height:3px;background:var(--teal)}

/* hero */
.hero{position:absolute;left:0;top:0;width:1200px;height:700px}
.hero-photo{position:absolute;inset:0;background:linear-gradient(125deg,#9a7f7a 0%,#8f8d93 30%,#9a8290 55%,#75828a 80%,#6f7a78 100%)}
.hero-shade{position:absolute;inset:0;background:rgba(30,30,35,.3)}
.nav{position:absolute;top:28px;left:0;width:1200px;font-size:13px;font-weight:700;color:var(--white)}
.nav a{color:var(--white);text-decoration:none;position:absolute;white-space:nowrap}
.nav a.current{color:var(--teal);text-decoration:underline}
.logo{position:absolute;font-family:var(--serif);color:var(--white);font-size:28px}
.cart-count{display:inline-flex;width:21px;height:21px;border-radius:50%;background:var(--white);color:var(--ink);font-size:12px;align-items:center;justify-content:center;margin-left:6px;vertical-align:middle}
.hero-title{position:absolute;top:262px;left:0;width:1200px;text-align:center;font-family:var(--serif);font-weight:400;font-size:50px;color:var(--white)}
.hero-text{position:absolute;top:347px;left:0;width:1200px;text-align:center;font-size:18px;line-height:25px;color:var(--white)}
.dots{position:absolute;top:637px;left:568px;display:flex;gap:6px}
.dots span{width:12px;height:12px;border-radius:50%;border:2px solid var(--white)}
.dots span.on{background:var(--teal)}

/* categories */
.category{position:absolute;top:824px;width:303px;text-align:center}
.category-photo{width:303px;height:299px}
.category h3{margin-top:22px;font-family:var(--serif);font-weight:400;font-size:18px;color:var(--ink)}
.category p{margin-top:10px;font-size:13px;line-height:19px;padding:0 28px}
.category .btn{position:relative;margin:20px auto 0;width:103px;height:31px;font-size:12px}

/* products */
.products{position:absolute;left:0;top:1321px;width:1200px;height:522px;background:var(--mint)}
.card{position:absolute;top:124px;width:221px;height:345px;background:var(--white);text-align:center}
.card-photo{width:221px;height:180px}
.card .name{margin-top:24px;font-family:var(--serif);font-size:13px;color:var(--ink);text-transform:uppercase}
.card .price{margin-top:14px;font-family:var(--serif);font-size:17px;color:var(--ink)}
.card .btn{position:relative;margin:14px auto 0;width:93px;height:27px;font-size:11px}

/* collections */
.collections{position:absolute;left:0;top:1843px;width:1200px;height:400px}
.collections-photo{position:absolute;inset:0;background:linear-gradient(90deg,#c98a3e 0%,#d39a4f 30%,#c98a44 55%,#b9885a 75%,#a98e7c 100%)}
.collections h2{position:absolute;left:141px;top:63px;font-family:var(--serif);font-weight:400;font-size:40px;color:var(--white)}
.collections p{position:absolute;left:143px;top:126px;width:360px;font-size:18px;line-height:26px;color:var(--white)}

/* mission */
.mission-text{position:absolute;left:233px;top:2368px;width:734px;text-align:center;font-size:16.5px;line-height:24px;color:var(--body)}

/* footer */
.footer{position:absolute;left:0;top:2563px;width:1200px;height:167px;background:var(--teal);color:var(--white)}
.footer .logo{left:131px;top:30px;font-size:28px}
.footer-nav a{position:absolute;top:44px;color:var(--white);text-decoration:none;font-size:13px;font-weight:700}
.follow{position:absolute;left:858px;top:45px;font-size:13px;font-weight:700}
.social{position:absolute;top:45px;font-size:13px;font-weight:700;color:var(--white);text-decoration:none}
.footer-rule{position:absolute;left:131px;top:92px;width:938px;height:1px;background:rgba(255,255,255,.8)}
.copyright{position:absolute;left:0;top:126px;width:1200px;text-align:center;font-size:11px}
</style>
</head>
<body>
<div class="page">

  <header class="hero">
    <div class="hero-photo" role="img" aria-label="Flat lay of colourful office supplies: scissors, markers, paper clips, sticky tabs and a stapler"></div>
    <div class="hero-shade"></div>
    <nav class="nav">
      <a class="current" style="left:131px">Home</a>
      <a style="left:191px">About Us</a>
      <a style="left:276px">Products</a>
      <a style="left:358px">Blog</a>
      <a style="left:407px">Contact Us</a>
      <a style="left:879px">Login</a>
      <a style="left:944px">Search</a>
      <a style="left:1011px;top:-3px">Cart<span class="cart-count">0</span></a>
    </nav>
    <div class="logo" style="left:583px;top:18px">Dultavo</div>
    <h1 class="hero-title">Office Supplies</h1>
    <p class="hero-text">There are many variations of passages of Lorem Ipsum available,<br>but the majority have suffered alteration in some form</p>
    <a class="btn" style="left:523px;top:428px;width:155px;height:45px;font-size:18px">Shop Now</a>
    <div class="dots"><span></span><span class="on"></span><span></span><span></span></div>
  </header>

  <section class="categories">
    <h2 class="heading" style="top:733px">Categories</h2>
    <div class="rule" style="top:782px"></div>
    <div class="category" style="left:133px">
      <div class="category-photo" role="img" aria-label="Rows of coloured pencils, pens and highlighters on a wooden desk" style="background:linear-gradient(135deg,#c98b3c 0%,#d39846 50%,#c7803a 100%)"></div>
      <h3>Office Supplies</h3>
      <p>Lorem Ipsum is simply dummy text of the printing and typesetting industry</p>
      <a class="btn">Shop Now</a>
    </div>
    <div class="category" style="left:450px">
      <div class="category-photo" role="img" aria-label="Kraft cardboard shipping boxes on a white background" style="background:linear-gradient(160deg,#e6d6c0 0%,#f3efe9 50%,#e4d3bc 100%)"></div>
      <h3>Packing Supplies</h3>
      <p>Lorem Ipsum is simply dummy text of the printing and typesetting industry</p>
      <a class="btn">Shop Now</a>
    </div>
    <div class="category" style="left:766px">
      <div class="category-photo" role="img" aria-label="Home appliances including washing machine, oven, fridge and vacuum in a grey room" style="background:linear-gradient(180deg,#8f8f91 0%,#b3b3b5 60%,#b89470 100%)"></div>
      <h3>Home Consumables</h3>
      <p>Lorem Ipsum is simply dummy text of the printing and typesetting industry</p>
      <a class="btn">Shop Now</a>
    </div>
  </section>

  <section class="products">
    <h2 class="heading" style="top:34px">Our Products</h2>
    <div class="rule" style="top:79px"></div>
    <div class="card" style="left:133px">
      <div class="card-photo" role="img" aria-label="Rolls of packing tape" style="background:linear-gradient(180deg,#f4f8e4,#e8f0c4)"></div>
      <div class="name">Lorem Ikpsum</div><div class="price">$25.00</div><a class="btn">Add to cart</a>
    </div>
    <div class="card" style="left:372px">
      <div class="card-photo" role="img" aria-label="Stainless steel double-door refrigerator" style="background:linear-gradient(180deg,#f2f2f3,#dcdcde)"></div>
      <div class="name">Lorem Ikpsum</div><div class="price">$25.00</div><a class="btn">Add to cart</a>
    </div>
    <div class="card" style="left:610px">
      <div class="card-photo" role="img" aria-label="Wooden ruler, pencil and eraser" style="background:linear-gradient(180deg,#f8f1e4,#ecdcc0)"></div>
      <div class="name">Lorem Ikpsum</div><div class="price">$25.00</div><a class="btn">Add to cart</a>
    </div>
    <div class="card" style="left:849px">
      <div class="card-photo" role="img" aria-label="Pair of black-handled scissors" style="background:linear-gradient(180deg,#f3f3f4,#dfe0e2)"></div>
      <div class="name">Lorem Ikpsum</div><div class="price">$25.00</div><a class="btn">Add to cart</a>
    </div>
  </section>

  <section class="collections">
    <div class="collections-photo" role="img" aria-label="Household appliances — heater, oven, microwave, washer, fridge and iron — against an ochre wall on a wooden floor"></div>
    <h2>Collections</h2>
    <p>Lorem Ipsum is simply dummy text of the printing and typesetting industry</p>
    <a class="btn" style="left:143px;top:205px;width:138px;height:40px;font-size:16px">Shop Now</a>
  </section>

  <section class="mission">
    <h2 class="heading" style="top:2280px">Mission</h2>
    <div class="rule" style="top:2329px"></div>
    <p class="mission-text">There are many variations of passages of Lorem Ipsum available, but the majority have suffered alteration in some form, by injected humour, or randomised words which don't look even slightly believable. If you are going to use a passage of Lorem Ipsum, you need to be sure there isn't anything embarrassing hidden in the middle of text. All the Lorem Ipsum generators on the Internet tend to repeat predefined chunks as necessary, making this the first true generator on the Internet. It uses a dictionary of over 200 Latin words, combined with a handful of model .</p>
  </section>

  <footer class="footer">
    <div class="logo">Dultavo</div>
    <nav class="footer-nav">
      <a style="left:333px">Home</a>
      <a style="left:393px">About Us</a>
      <a style="left:478px">Products</a>
      <a style="left:560px">Blog</a>
      <a style="left:609px">Contact Us</a>
    </nav>
    <div class="follow">Follow us</div>
    <a class="social" style="left:938px">Vexo</a>
    <a class="social" style="left:976px">Lumo</a>
    <a class="social" style="left:1016px">Pikra</a>
    <a class="social" style="left:1057px">Tubo</a>
    <div class="footer-rule"></div>
    <div class="copyright">Copyright © 2022 All Rights Reserved</div>
  </footer>

</div>
</body>
</html>
```